CLAIM GUARD PLAN

I'm virtually ready to launch my site, but I have a number of edits and modifications that need to be implemented. More importantly, I'm always looking to improve my site, particularly now that I am making my proverbial "FIRST IMPRESSION." Thus, I'm willing to see if there is someone who can add creativity and perhaps improve what I already have, particularly on the All Important Front Page.

```html
<!DOCTYPE html>
<html lang="en">
<head>
<meta charset="utf-8">
<title>Claim Guard Plan</title>
<link href="https://fonts.googleapis.com/css2?family=Libre+Baskerville:wght@400;700&family=Roboto:wght@400;500&display=swap" rel="stylesheet">
<style>
:root{
  --teal:#0f7d87;
  --red:#b3121f;
  --navy:#151d2b;
  --navy-deep:#0f1621;
  --ink:#2b2b2b;
  --muted:#5a5a5a;
  --light:#f3f3f3;
  --line:#d9d9d9;
  --white:#ffffff;
}
*{box-sizing:border-box;margin:0;padding:0}
html,body{width:1200px;height:5352px;overflow:hidden}
body{font-family:"Libre Baskerville",Georgia,serif;color:var(--ink);background:var(--white);position:relative}
.abs{position:absolute}
/* hero */
.hero{position:absolute;left:0;top:0;width:1200px;height:870px;color:var(--white);overflow:hidden}
.hero-photo{position:absolute;inset:0;background:linear-gradient(180deg,#2a2118 0%,#4a3423 30%,#3a2a1e 55%,#1e1712 100%)}
.hero-shade{position:absolute;inset:0;background:linear-gradient(180deg,rgba(0,0,0,.35),rgba(0,0,0,.1) 40%,rgba(0,0,0,.55))}
.topbar{position:absolute;left:112px;right:112px;top:20px;height:50px;display:flex;justify-content:space-between;font-size:14px;line-height:24px}
.topbar .item{display:flex;gap:16px;align-items:center}
.mainnav{position:absolute;left:112px;right:112px;top:100px;display:flex;justify-content:space-between;font-size:17px}
.mainnav .side{display:flex;gap:26px;align-items:center}
.mainnav .dot{width:6px;height:6px;border-radius:50%;border:1px solid rgba(255,255,255,.6)}
.navrule{position:absolute;left:0;right:0;top:150px;border-top:1px solid rgba(255,255,255,.15)}
.brand-mark{position:absolute;left:525px;top:18px;width:150px;height:150px;border-radius:50%;background:var(--white);display:flex;align-items:center;justify-content:center;text-align:center;font-size:15px;font-weight:700;color:var(--red);line-height:20px;padding:20px}
.hero-title{position:absolute;left:0;right:0;top:190px;text-align:center;font-size:28px;font-weight:700;letter-spacing:.5px}
.hero-copy{position:absolute;left:112px;top:570px;width:950px}
.hero-copy h2{font-size:26px;font-weight:400;letter-spacing:1px;margin-bottom:18px}
.hero-copy p{font-size:15.5px;line-height:29px;color:#e9e4de}
.btns{position:absolute;left:112px;top:768px;display:flex;gap:24px}
.btn{height:52px;display:flex;align-items:center;justify-content:center;font-size:13px;padding:0 26px}
.btn-teal{background:var(--teal);color:var(--white);width:280px}
.btn-white{background:var(--white);color:var(--ink);width:146px}
/* about */
.section-title{position:absolute;left:0;right:0;text-align:center;font-size:26px;letter-spacing:1px;color:#222}
.about-pill{position:absolute;left:110px;top:959px;width:976px;height:189px;background:#efefef;border-radius:95px}
.about-pill .seal{position:absolute;left:22px;top:22px;width:145px;height:145px;border-radius:50%;background:var(--white);display:flex;align-items:center;justify-content:center;text-align:center;color:var(--red);font-weight:700;font-size:14px;line-height:19px;padding:18px}
.about-pill .txt{position:absolute;left:196px;top:36px;width:760px;font-family:"Roboto",Arial,sans-serif;font-size:17px;line-height:31px;color:#222}
.t{color:var(--teal)}
.r{color:var(--red)}
.about-pill .tag{margin-top:10px;font-family:"Libre Baskerville",Georgia,serif;font-size:14.5px;color:var(--red)}
.quote-card{position:absolute;left:112px;top:1208px;width:473px;height:683px;background:#1b1b1b;color:var(--white)}
.quote-photo{position:absolute;inset:0;background:linear-gradient(160deg,#3b2a1c 0%,#2a1e15 45%,#120e0b 100%)}
.quote-frame{position:absolute;left:16px;top:16px;right:16px;bottom:16px;border:1px solid rgba(255,255,255,.35)}
.quote-text{position:absolute;left:32px;top:548px;font-size:26px;line-height:32px}
.quote-by{position:absolute;right:42px;top:628px;font-size:15px;display:flex;align-items:center;gap:12px}
.quote-by span{display:block;width:44px;border-top:1px solid #fff}
.about-body{position:absolute;left:614px;top:1204px;width:470px;font-size:15.5px;line-height:32.5px;color:#222}
.about-body p{margin-bottom:22px}
/* services */
.services{position:absolute;left:0;top:1983px;width:1200px;height:1779px;background:var(--light)}
.services-intro{position:absolute;left:200px;width:800px;top:2085px;text-align:center;font-size:19px;line-height:36px;color:#333}
.card{position:absolute;width:473px;background:var(--white)}
.card .ph{height:287px;width:100%}
.card .arrow{position:absolute;right:20px;top:255px;width:58px;height:58px;border-radius:50%;background:var(--white);display:flex;align-items:center;justify-content:center;box-shadow:0 2px 6px rgba(0,0,0,.12)}
.card.active .arrow{background:var(--teal)}
.card.active{border-bottom:8px solid var(--teal)}
.card h3{font-size:15px;font-weight:400;letter-spacing:.3px;margin:22px 20px 14px;color:#222}
.card p{font-size:12.5px;line-height:25px;color:var(--muted);margin:0 20px 22px}
/* contact */
.contact{position:absolute;left:0;top:3762px;width:1200px;height:411px;background:linear-gradient(180deg,var(--navy) 0%,var(--navy-deep) 100%);color:var(--white)}
.contact h2{position:absolute;left:0;right:0;top:68px;text-align:center;font-size:26px;font-weight:400;letter-spacing:1px}
.contact p{position:absolute;left:240px;width:720px;top:128px;text-align:center;font-size:15.5px;line-height:36px;color:#d8dbe2}
.cta{position:absolute;top:228px;height:76px;width:310px;display:flex;border:1px solid rgba(255,255,255,.35)}
.cta .ic{width:76px;height:100%;background:var(--teal);display:flex;align-items:center;justify-content:center}
.cta .lbl{flex:1;display:flex;align-items:center;padding-left:28px;font-size:24px}
.stars{position:absolute;left:0;right:0;top:346px;text-align:center;font-size:18px;letter-spacing:6px}
/* faq */
.faq{position:absolute;left:228px;width:742px;border:1px solid var(--line);background:var(--white)}
.faq .row{display:flex;align-items:center;height:62px;padding:0 20px;gap:22px;font-size:15px;color:#333}
.faq .q{width:22px;height:22px;border-radius:50%;background:var(--teal);color:#fff;font-family:"Roboto",Arial,sans-serif;font-size:13px;font-weight:700;display:flex;align-items:center;justify-content:center;flex:none}
.faq .pm{margin-left:auto;color:#aaa;font-size:24px;font-family:"Roboto",Arial,sans-serif}
.faq.open .row{height:auto;align-items:flex-start;padding-top:22px;color:var(--teal);font-size:17px;line-height:26px}
.faq.open .ans{padding:14px 20px 22px 64px;font-size:13px;line-height:26px;color:#444}
/* footer */
.footer{position:absolute;left:0;top:4951px;width:1200px;height:401px;background:linear-gradient(180deg,#111923,#0b1118);color:var(--white)}
.footer .brand-mark{top:-20px;left:530px;width:140px;height:140px;font-size:14px}
.foot-nav{position:absolute;left:112px;right:112px;top:148px;display:flex;justify-content:space-between;align-items:center;font-size:17px}
.foot-nav .dot{width:6px;height:6px;border-radius:50%;border:1px solid rgba(255,255,255,.5)}
.foot-rule{position:absolute;left:0;right:0;top:205px;border-top:1px solid rgba(255,255,255,.12)}
.foot-info{position:absolute;left:112px;right:112px;top:230px;display:flex;justify-content:space-between;align-items:center;font-size:14px;line-height:24px}
.foot-info .item{display:flex;gap:18px;align-items:center}
.social{display:flex;gap:30px}
.social span{width:36px;height:36px;border-radius:50%;background:#9aa0a8;display:block}
.copy{position:absolute;left:0;right:0;top:338px;text-align:center;font-size:11px;color:#5d6672}
</style>
</head>
<body>

<header class="hero">
  <div class="hero-photo" role="img" aria-label="Courtroom with a judge at the bench and attorneys in warm window light"></div>
  <div class="hero-shade"></div>
  <div class="topbar">
    <div class="item">
      <svg width="18" height="24" viewBox="0 0 18 24"><path d="M9 0C4 0 0 4 0 9c0 6 9 15 9 15s9-9 9-15c0-5-4-9-9-9zm0 12a3 3 0 110-6 3 3 0 010 6z" fill="#fff"/></svg>
      <div>4870 Desert Ridge Ave., Suite<br>210 Mesa, Arizona 85201</div>
    </div>
    <div class="item" style="font-size:17px">
      <svg width="20" height="20" viewBox="0 0 24 24"><path d="M6.6 10.8a15 15 0 006.6 6.6l2.2-2.2a1 1 0 011-.25 11.4 11.4 0 003.6.57 1 1 0 011 1V20a1 1 0 01-1 1A17 17 0 013 4a1 1 0 011-1h3.5a1 1 0 011 1c0 1.25.2 2.45.57 3.6a1 1 0 01-.25 1z" fill="#fff"/></svg>
      480.555.0142 / 800.555.0199
    </div>
  </div>
  <nav class="mainnav">
    <div class="side"><span>Home</span><i class="dot"></i><span>About</span><i class="dot"></i><span>Services</span></div>
    <div class="side"><span>Faq</span><i class="dot"></i><span>Contact Us</span><i class="dot"></i><span>Free Consulation</span></div>
  </nav>
  <div class="navrule"></div>
  <div class="brand-mark">Claim Guard Plan</div>
  <h1 class="hero-title">CLAIM GUARD PLAN</h1>
  <div class="hero-copy">
    <h2>BUSINESS OWNERS:</h2>
    <p>Claim Guard Plan (CGP) is an extremely affordable legal service plan (as little as $8.00 per month) that INSULATES business owners from unwarranted LEGAL CLAIMS and expensive LAWSUITS. Our plan uses local, experienced, quality attorneys who focus on PROBLEM PREVENTION using proprietary tools available only to CGP members. Contact us for a free consultation and receive a FREE OVERVIEW of your business to see if you are truly insulated from legal claims.</p>
  </div>
  <div class="btns">
    <div class="btn btn-teal">SCHEDULE FREE CONSULATION</div>
    <div class="btn btn-white">LEARN MORE</div>
  </div>
</header>

<section class="about">
  <h2 class="section-title" style="top:908px">ABOUT US</h2>
  <div class="about-pill">
    <div class="seal">Claim Guard Plan</div>
    <div class="txt">
      <span class="t">CGP</span> is a group of attorney and legal assistants with many years of experience in litigation, who are devoted to <span class="t">PREVENTING LEGAL CLAIMS</span> and <span class="t">COSTLY LAWSUITS</span> through a variety of <span class="t">FREE</span> and <span class="t">VERY AFFORDABLE</span> services described below.
      <div class="tag">OUR UNIQUE SERVICE PLAN MAKES IT POSSIBLE FOR US TO HALT THE LAWSUITS.</div>
    </div>
  </div>
  <div class="quote-card">
    <div class="quote-photo" role="img" aria-label="Attorney in a robe reading papers on the phone in a library office"></div>
    <div class="quote-frame"></div>
    <div class="quote-text">An OUNCE of PREVENTION<br>is worth a POUND of CURE.</div>
    <svg class="abs" style="left:420px;top:562px" width="38" height="30" viewBox="0 0 38 30"><path d="M0 30V16C0 7 5 1 14 0v6c-4 1-6 4-6 8h6v16zm22 0V16c0-9 5-15 14-16v6c-4 1-6 4-6 8h6v16z" fill="#fff"/></svg>
    <div class="quote-by"><span></span>Elias Thornbury.</div>
  </div>
  <div class="about-body">
    <p>A homebuilding company was sued by a former employee who claimed to have been promised a more favorable sales area, which claim was disputed by the homebuilder. There was no evidence that such a promise had been made, other than the plaintiff's oral testimony. The company had the case dismissed, but spent <b>$10,000</b> defending the case.</p>
    <p>And even though it was awarded its attorney's fees, the plaintiff proved uncollectible. Had the company been an <b>CGP</b> member, the case likely would never have been filed. Call for your <b>FREE CONSULTATION</b> and let us show you why the plaintiff likely would not have found a contingency attorney (as was the case) or been able to pay an attorney on an hourly basis. In short, by using CGP's services, the plaintiff's claim would not have been filed.</p>
    <p>In our vast experience with commercial litigation, we believe that a very large percentage of litigation cases hinge on "he said / she said" issues. By using CGP's services, we believe we can <b>INSULATE</b> you and your business from all such issues, which will <b>MINIMIZE</b> your <b>EXPOSURE</b> to <b>LEGAL CLAIMS</b> and <b>LAWSUITS</b></p>
  </div>
</section>

<section class="services">
</section>
<h2 class="section-title" style="top:2033px">OUR SERVICES</h2>
<p class="services-intro">The price for a membership is a ridiculously low <span class="t">$9.95 PER WEEK.</span> We believe that this fee is very affordable. So what is it? Membership includes the following:</p>

<article class="card active" style="left:114px;top:2205px">
  <div class="ph" role="img" aria-label="Business handshake across a desk" style="background:linear-gradient(135deg,#3a3d44,#8d8a86 55%,#d9d4cc)"></div>
  <div class="arrow"><svg width="22" height="14" viewBox="0 0 22 14"><path d="M0 7h20M14 1l6 6-6 6" stroke="#fff" stroke-width="2" fill="none"/></svg></div>
  <h3>FREE INITIAL CONSULTATION</h3>
  <p>As a prospective Claim Guard Plan ("CGP") member, we urge you to schedule an initial consultation with us – at no charge – where we will go over each of the services in detail, and offer an overview of your business formation at no charge.</p>
</article>
<article class="card" style="left:614px;top:2205px">
  <div class="ph" role="img" aria-label="Judge's gavel on a wooden desk beside documents" style="background:linear-gradient(135deg,#1e1510,#6b4528 55%,#b78758)"></div>
  <div class="arrow"><svg width="22" height="14" viewBox="0 0 22 14"><path d="M0 7h20M14 1l6 6-6 6" stroke="#222" stroke-width="2" fill="none"/></svg></div>
  <h3>PROPRIETARY CONTRACT LANGUAGE</h3>
  <p>As a prospective Claim Guard Plan ("CGP") member, we urge you to schedule an initial consultation with us – at no charge – where we will go over each of the services in detail, and offer an overview of your business formation at no charge.</p>
</article>
<article class="card" style="left:114px;top:2722px">
  <div class="ph" role="img" aria-label="Fountain pen resting on a signed document" style="background:linear-gradient(135deg,#3a2a1c,#a08466 55%,#e0cfb6)"></div>
  <div class="arrow"><svg width="22" height="14" viewBox="0 0 22 14"><path d="M0 7h20M14 1l6 6-6 6" stroke="#222" stroke-width="2" fill="none"/></svg></div>
  <h3>FREE CONSULTATION</h3>
  <p>As a prospective Claim Guard Plan ("CGP") member, we urge you to schedule an initial consultation with us – at no charge – where we will go over each of the services in detail, and offer an overview of your business formation at no charge.</p>
</article>
<article class="card" style="left:614px;top:2722px">
  <div class="ph" role="img" aria-label="Attorney in a suit reviewing letters" style="background:linear-gradient(135deg,#1d2a3c,#3e5068 50%,#c9ccd2)"></div>
  <div class="arrow"><svg width="22" height="14" viewBox="0 0 22 14"><path d="M0 7h20M14 1l6 6-6 6" stroke="#222" stroke-width="2" fill="none"/></svg></div>
  <h3>FREE ATTORNEY LETTERS</h3>
  <p>As a prospective Claim Guard Plan ("CGP") member, we urge you to schedule an initial consultation with us – at no charge – where we will go over each of the services in detail, and offer an overview of your business formation at no charge.</p>
</article>
<article class="card" style="left:114px;top:3216px">
  <div class="ph" role="img" aria-label="Gavel resting on a pile of banknotes" style="background:linear-gradient(135deg,#b99aa4,#8d6a55 50%,#d8c6c0)"></div>
  <div class="arrow"><svg width="22" height="14" viewBox="0 0 22 14"><path d="M0 7h20M14 1l6 6-6 6" stroke="#222" stroke-width="2" fill="none"/></svg></div>
  <h3>LITIGATION DISCOUNTS</h3>
  <p>As a prospective Claim Guard Plan ("CGP") member, we urge you to schedule an initial consultation with us – at no charge – where we will go over each of the services in detail, and offer an overview of your business formation at no charge.</p>
</article>
<article class="card" style="left:614px;top:3216px">
  <div class="ph" role="img" aria-label="Brass scales of justice and gavel on a dark background" style="background:linear-gradient(135deg,#0d1117,#2b2a26 55%,#6e5a3a)"></div>
  <div class="arrow"><svg width="22" height="14" viewBox="0 0 22 14"><path d="M0 7h20M14 1l6 6-6 6" stroke="#222" stroke-width="2" fill="none"/></svg></div>
  <h3>COLLECTIONS</h3>
  <p>As a prospective Claim Guard Plan ("CGP") member, we urge you to schedule an initial consultation with us – at no charge – where we will go over each of the services in detail, and offer an overview of your business formation at no charge.</p>
</article>

<section class="contact">
  <h2>CONTACT US FOR A FREE CONSULTATION</h2>
  <p>We Fight for Your Right. Without win, Don't Take Money.Lorem ipsum dolor sit amet, consectetur adipiscing elit. Ut elit tellus, luctus nec ullamcorper mattis, leo.</p>
  <div class="cta" style="left:114px">
    <div class="ic"><svg width="30" height="30" viewBox="0 0 24 24"><path d="M6.6 10.8a15 15 0 006.6 6.6l2.2-2.2a1 1 0 011-.25 11.4 11.4 0 003.6.57 1 1 0 011 1V20a1 1 0 01-1 1A17 17 0 013 4a1 1 0 011-1h3.5a1 1 0 011 1c0 1.25.2 2.45.57 3.6a1 1 0 01-.25 1z" fill="#fff"/></svg></div>
    <div class="lbl">480.555.0142</div>
  </div>
  <div class="cta" style="left:446px">
    <div class="ic"><svg width="30" height="30" viewBox="0 0 24 24"><path d="M6.6 10.8a15 15 0 006.6 6.6l2.2-2.2a1 1 0 011-.25 11.4 11.4 0 003.6.57 1 1 0 011 1V20a1 1 0 01-1 1A17 17 0 013 4a1 1 0 011-1h3.5a1 1 0 011 1c0 1.25.2 2.45.57 3.6a1 1 0 01-.25 1z" fill="#fff"/></svg></div>
    <div class="lbl">800.555.0199</div>
  </div>
  <div class="cta" style="left:778px">
    <div class="ic"><svg width="30" height="30" viewBox="0 0 24 24"><rect x="3" y="5" width="18" height="16" rx="2" fill="none" stroke="#fff" stroke-width="2"/><path d="M3 10h18M8 2v5M16 2v5" stroke="#fff" stroke-width="2"/><path d="M8 15l3 3 5-5" stroke="#fff" stroke-width="2" fill="none"/></svg></div>
    <div class="lbl">Free Consultation</div>
  </div>
  <div class="stars">★★★</div>
</section>

<section class="faqs">
  <h2 class="section-title" style="top:4255px">FREQUENTLY ASKED QUESTIONS</h2>
  <div class="faq" style="top:4343px"><div class="row"><span class="q">?</span>Why should I be concerned about legal claims?<span class="pm">+</span></div></div>
  <div class="faq" style="top:4428px"><div class="row"><span class="q">?</span>Provide more details about the value of CGP's contract language.<span class="pm">+</span></div></div>
  <div class="faq" style="top:4513px"><div class="row"><span class="q">?</span>What does an CGP membership cost?<span class="pm">+</span></div></div>
  <div class="faq open" style="top:4596px">
    <div class="row"><span class="q">?</span><span>If I'm a contractor, for example, how can an CGP<br>membership minimize legal claims against my business?</span><span class="pm">−</span></div>
    <div class="ans">Lorem ipsum dolor sit amet, consectetur adipiscing elit. Suspendisse varius enim in eros elementum tristique. Duis cursus, mi quis viverra ornare,</div>
  </div>
  <div class="faq" style="top:4777px"><div class="row"><span class="q">?</span>Do you have a Referral Program?<span class="pm">+</span></div></div>
</section>

<footer class="footer">
  <div class="brand-mark">Claim Guard Plan</div>
  <nav class="foot-nav">
    <span>Home</span><i class="dot"></i><span>About</span><i class="dot"></i><span>Services</span><i class="dot"></i><span>Faq</span><i class="dot"></i><span>Contact Us</span><i class="dot"></i><span>Terms Of Service</span><i class="dot"></i><span>Privacy Policy</span>
  </nav>
  <div class="foot-rule"></div>
  <div class="foot-info">
    <div class="item">
      <svg width="24" height="32" viewBox="0 0 18 24"><path d="M9 0C4 0 0 4 0 9c0 6 9 15 9 15s9-9 9-15c0-5-4-9-9-9zm0 12a3 3 0 110-6 3 3 0 010 6z" fill="#0f9aa6"/></svg>
      <div>4870 DESERT RIDGE AVE., SUITE 210,<br>MESA, ARIZONA 85201</div>
    </div>
    <div class="social"><span></span><span></span><span></span></div>
    <div class="item" style="font-size:16px">
      <svg width="24" height="24" viewBox="0 0 24 24"><path d="M6.6 10.8a15 15 0 006.6 6.6l2.2-2.2a1 1 0 011-.25 11.4 11.4 0 003.6.57 1 1 0 011 1V20a1 1 0 01-1 1A17 17 0 013 4a1 1 0 011-1h3.5a1 1 0 011 1c0 1.25.2 2.45.57 3.6a1 1 0 01-.25 1z" fill="#0f9aa6"/></svg>
      480.555.0142 / (800) 555-0177
    </div>
  </div>
  <div class="copy">2023 © All rights reserved by claimguardplan.com</div>
</footer>

</body>
</html>
```